Car rental website design for a UAE car rental company

This project is about creating a new website design for a car rental company located in Dubai (United Arab Emirates), I opened the same project a few months ago but I didn't receive a lot of appealing entries so I closed it but this time I am marking the project as guaranteed to avoid such situation again, if you have already provided a design before then please re-submit again on this project so that it is considered while reviewing all the designs

A few important things:

1- We need a simple non-complex design
2- The final deliverable would be 2 screens (PSD, JPEG ... etc), the first screen is for the home page and the second screen is for an internal page
3- The home page must have a section that end users can use to rent a car online directly from the home page instead of going into some inner pages
4- The current website is very old and not very appealing so avoid creating a similar design (www.crestvane-autos.example)
5- The name is Crestvane but the company rents normal cars (no Limousin cars will be rented) so avoid adding any fancy cars in the images/graphics used in the design, just normal end users cars
6- The expected pages would be: home, About us, Our team, Strategy, Contact us and links to social media pages
7- The attachments include the company's logo and some screens from other car rental companies that provide online rentals/payments

If you have any questions please feel free to ask and please note that we will need the designs urgently

Thanks

Target Market(s)

Dubai - United Arab Emirates

Industry/Entity Type

It Company

Number of Pages Required

2 page

Font styles to use
Sans Serif

Requirements
Must have
• Check the project details
Nice to have
Should not have

```html
<!DOCTYPE html>
<html lang="en">
<head>
<meta charset="utf-8">
<title>Crestvane Rent A Car</title>
<link href="https://fonts.googleapis.com/css2?family=Roboto:wght@400;500;700;900&family=Roboto+Condensed:wght@700&family=Open+Sans:wght@400&display=swap" rel="stylesheet">
<style>
:root{
  --crimson:#a0102a;
  --crimson-dark:#7d0b20;
  --ink:#111;
  --hero-dark:#2a2828;
  --hero-mid:#6a6766;
  --panel:#272727;
  --cell:#333;
  --cell-line:#1f1f1f;
  --field:#1c1c1c;
  --muted:#8a8a8a;
  --footer:#1b1b1b;
  --white:#fff;
}
*{box-sizing:border-box;margin:0;padding:0}
html,body{width:780px;height:1200px;overflow:hidden;background:#000}
body{position:relative;font-family:"Roboto",Arial,sans-serif;color:var(--white)}
.hero{position:absolute;left:0;top:0;width:780px;height:437px;
  background:radial-gradient(ellipse at 55% 45%,var(--hero-mid) 0%,#4a4746 35%,var(--hero-dark) 75%,#1a1919 100%)}
.brand{position:absolute;left:72px;top:16px;width:130px;text-align:center}
.brand-mark{display:block;width:50px;height:56px;margin:0 auto 8px;background:var(--white);border:2px solid var(--crimson)}
.brand-name{display:block;font-size:24px;font-weight:500;color:#cfcfcf;line-height:1}
.brand-sub{display:block;font-size:10px;letter-spacing:3px;color:var(--crimson);margin-top:3px}
.main-nav{position:absolute;left:196px;top:14px;height:24px;display:flex;background:var(--crimson)}
.main-nav a{color:var(--white);text-decoration:none;font-family:Arial,sans-serif;font-size:11.5px;line-height:24px;padding:0 14px;border-right:1px solid var(--crimson-dark)}
.main-nav a:last-child{border-right:0;padding-right:20px}
.menu-icon{position:absolute;left:693px;top:20px}
.lang{position:absolute;left:719px;top:18px;width:47px;height:15px;border:1px solid #999;font-size:6px;color:#ddd;line-height:13px;padding-left:7px}
.lang::after{content:"▾";position:absolute;right:3px;top:0;font-size:7px}
.slide-dots{position:absolute;left:740px;top:180px;display:flex;flex-direction:column;gap:4px}
.slide-dots span{width:7px;height:7px;border:1px solid #777}
.slide-dots span:first-child{background:#777}
.play{position:absolute;left:368px;top:182px}
.play-label{position:absolute;left:340px;top:234px;width:100px;text-align:center;font-size:7.5px}
.booking-box{position:absolute;left:28px;top:326px;width:270px;height:90px;background:rgba(30,30,30,.88);border:1px solid #555;border-bottom:2px solid var(--crimson);padding:5px 7px}
.booking-box .kicker{font-size:10px;color:#ddd;letter-spacing:.2px}
.booking-box .headline{font-family:"Roboto Condensed",sans-serif;font-size:13px;color:#ccc;margin-top:1px}
.booking-fields{display:flex;gap:4px;margin-top:5px}
.field{flex:1;height:18px;background:var(--field);border:1px solid #555;font-size:6.5px;color:#aaa;line-height:16px;padding-left:4px}
.field.wide{flex:1.3}
.btn-red{display:inline-block;background:var(--crimson);color:var(--white);font-size:7.5px;text-decoration:none;text-align:center}
.booking-box .btn-red{margin-top:5px;line-height:18px;width:81px;border:1px solid #c0304a}
.scroll-hint{position:absolute;left:330px;top:370px;width:120px;text-align:center;font-size:7.5px}
.scroll-hint svg{display:block;margin:0 auto 8px}
.tagline{position:absolute;left:515px;top:351px}
.tagline-banner{width:169px;height:32px;background:#3a3838;border:1px solid var(--crimson);text-align:center;font-family:"Roboto Condensed",sans-serif;font-size:14px;line-height:30px}
.tagline-text{margin-top:5px;font-size:14px;font-weight:500;letter-spacing:.3px;white-space:nowrap}
.welcome{position:absolute;left:0;top:437px;width:780px;height:190px;background:var(--white);text-align:center;color:var(--ink)}
.welcome h1{font-size:14.5px;font-weight:700;letter-spacing:.6px;margin-top:41px}
.welcome .btn-red{margin-top:7px;line-height:20px;width:79px}
.lede{font-family:"Open Sans",sans-serif;font-size:6.6px;line-height:14px;color:var(--muted);width:500px;margin:20px auto 0;text-transform:uppercase;text-align:center}
.featured{position:absolute;left:0;top:627px;width:780px;height:522px;
  background:radial-gradient(ellipse at 50% 60%,#2a2a2a 0%,#0d0d0d 55%,#000 100%)}
.featured h2{text-align:center;font-size:14.5px;font-weight:700;letter-spacing:.8px;margin-top:31px}
.featured .lede{margin-top:17px;width:500px;color:#9a9a9a}
.car-grid{position:absolute;left:112px;top:121px;display:flex;gap:1px}
.car-card{width:185px;height:356px;background:var(--panel)}
.car-photo{height:117px}
.car-photo.silver{background:linear-gradient(160deg,#9aa0a6,#4a4f55 60%,#2a2d30)}
.car-photo.yellow{background:linear-gradient(160deg,#1e2a3a,#3a3a30 50%,#c9a31a 75%,#2a2a2a)}
.car-photo.red{background:linear-gradient(170deg,#b9a98e,#6c5648 45%,#8a2030 70%,#555 100%)}
.car-body{padding:13px 15px 0 16px}
.car-body h3{font-size:11px;font-weight:500}
.car-body .price{font-size:8.5px;font-weight:500;margin-top:6px}
.specs{width:154px;margin-top:7px;border-collapse:collapse;font-size:6.6px;color:#ddd}
.specs td{background:var(--cell);height:19.5px;padding-left:8px;border-bottom:2px solid var(--cell-line)}
.specs td:first-child{width:77px;border-right:2px solid var(--cell-line)}
.btn-outline{display:block;width:153px;height:28px;margin-top:6px;border:1px solid #9a9a9a;text-align:center;line-height:26px;font-size:7.3px;font-weight:500;color:#aaa;text-decoration:none;letter-spacing:.3px}
.site-footer{position:absolute;left:0;top:1149px;width:780px;height:51px;background:var(--footer);color:var(--muted);font-family:Arial,sans-serif;font-size:8.5px}
.footer-nav{position:absolute;left:110px;top:10px}
.footer-nav a{color:var(--muted);text-decoration:none}
.footer-nav span{margin:0 5px}
.copyright{position:absolute;left:110px;top:29px}
.social{position:absolute;left:539px;top:17px;display:flex;gap:6px}
.social a{width:18px;height:18px;border-radius:50%;background:#d8d8d8}
</style>
</head>
<body>
<header class="hero" role="img" aria-label="Silver sedan in motion on a dark road">
  <div class="brand"><span class="brand-mark"></span><span class="brand-name">Crestvane</span><span class="brand-sub">Rent A Car</span></div>
  <nav class="main-nav">
    <a href="#">Home</a><a href="#">About us</a><a href="#">Our team</a><a href="#">Strategy</a><a href="#">Vehicles</a><a href="#">Contact us</a>
  </nav>
  <svg class="menu-icon" width="16" height="12" viewBox="0 0 16 12"><rect y="0" width="16" height="2" fill="#ccc"/><rect y="5" width="16" height="2" fill="#ccc"/><rect y="10" width="16" height="2" fill="#ccc"/></svg>
  <div class="lang">ENGLISH</div>
  <div class="slide-dots"><span></span><span></span><span></span><span></span><span></span></div>
  <svg class="play" width="44" height="44" viewBox="0 0 44 44"><circle cx="22" cy="22" r="20" fill="none" stroke="rgba(255,255,255,.35)" stroke-width="2"/><path d="M18 14 L30 22 L18 30 Z" fill="rgba(255,255,255,.35)"/></svg>
  <div class="play-label">PLAY VIDEO</div>
  <form class="booking-box">
    <div class="kicker">A BOOKING FROM TO</div>
    <div class="headline">RENT A CAR</div>
    <div class="booking-fields">
      <div class="field wide">Pick-up: Dubai ▾</div>
      <div class="field">From: date</div>
      <div class="field">To: date</div>
    </div>
    <a class="btn-red" href="#">BOOK NOW</a>
  </form>
  <div class="scroll-hint">
    <svg width="12" height="12" viewBox="0 0 12 12"><path d="M2 1 L6 5 L10 1 M2 6 L6 10 L10 6" fill="none" stroke="#aaa" stroke-width="1.5"/></svg>
    SCROLL DOWN FOR MORE
  </div>
  <div class="tagline">
    <div class="tagline-banner">RENT A CAR</div>
    <div class="tagline-text">WE ARE A CAR RENTAL COMPANY</div>
  </div>
</header>

<section class="welcome">
  <h1>WELCOME TO CRESTVANE RENT A CAR</h1>
  <a class="btn-red" href="#">READ MORE</a>
  <p class="lede">Crestvane Rent A Car is a Dubai rental company offering everyday sedans, hatchbacks and family SUVs for business trips, holidays, city drives or whatever you need. We are known for friendly service and fair prices, and every car you get from us is clean, checked and ready to drive!</p>
</section>

<section class="featured">
  <h2>FEATURED CARS</h2>
  <p class="lede">Choose from our most popular everyday cars, all well kept and fully insured, with easy pick-up across Dubai and online booking in a few clicks. Simple rates, no hidden fees and help whenever you need it.</p>
  <div class="car-grid">
    <article class="car-card">
      <div class="car-photo silver" role="img" aria-label="Silver sedan in a tunnel"></div>
      <div class="car-body">
        <h3>ECONOMY SEDAN</h3>
        <p class="price">PRICE PER DAY : AED 150</p>
        <table class="specs"><tr><td>Car type</td><td>Sedan</td></tr><tr><td>Seats</td><td>5</td></tr><tr><td>Doors</td><td>4</td></tr><tr><td>Min. driver age</td><td>21</td></tr><tr><td>Transmission</td><td>Automatic</td></tr><tr><td>Air conditioning</td><td>Yes</td></tr><tr><td>Unlimited km?</td><td>No</td></tr></table>
        <a class="btn-outline" href="#">READ MORE ABOUT THE CAR</a>
      </div>
    </article>
    <article class="car-card">
      <div class="car-photo yellow" role="img" aria-label="Yellow hatchback in a garage"></div>
      <div class="car-body">
        <h3>COMPACT HATCHBACK</h3>
        <p class="price">PRICE PER DAY : AED 130</p>
        <table class="specs"><tr><td>Car type</td><td>Hatchback</td></tr><tr><td>Seats</td><td>5</td></tr><tr><td>Doors</td><td>5</td></tr><tr><td>Min. driver age</td><td>21</td></tr><tr><td>Transmission</td><td>Automatic</td></tr><tr><td>Air conditioning</td><td>Yes</td></tr><tr><td>Unlimited km?</td><td>No</td></tr></table>
        <a class="btn-outline" href="#">READ MORE ABOUT THE CAR</a>
      </div>
    </article>
    <article class="car-card">
      <div class="car-photo red" role="img" aria-label="Red SUV on a mountain road"></div>
      <div class="car-body">
        <h3>FAMILY SUV</h3>
        <p class="price">PRICE PER DAY : AED 220</p>
        <table class="specs"><tr><td>Car type</td><td>SUV</td></tr><tr><td>Seats</td><td>5</td></tr><tr><td>Doors</td><td>5</td></tr><tr><td>Min. driver age</td><td>23</td></tr><tr><td>Transmission</td><td>Automatic</td></tr><tr><td>Air conditioning</td><td>Yes</td></tr><tr><td>Unlimited km?</td><td>Yes</td></tr></table>
        <a class="btn-outline" href="#">READ MORE ABOUT THE CAR</a>
      </div>
    </article>
  </div>
</section>

<footer class="site-footer">
  <nav class="footer-nav">
    <a href="#">Home</a><span>|</span><a href="#">About us</a><span>|</span><a href="#">Our team</a><span>|</span><a href="#">Strategy</a><span>|</span><a href="#">Vehicles</a><span>|</span><a href="#">Contact us</a>
  </nav>
  <p class="copyright">Copyright© crestvanerentacar.example,2015, All Right Reserved.</p>
  <div class="social" aria-label="Social media links"><a href="#" aria-label="Social link 1"></a><a href="#" aria-label="Social link 2"></a><a href="#" aria-label="Social link 3"></a><a href="#" aria-label="Social link 4"></a><a href="#" aria-label="Social link 5"></a></div>
</footer>
</body>
</html>
```